Management Consultancy needs sharp professional services showcased in a brochure

We are a management consultancy specializing on contract management and conflict avoidance services requiring a professional brochure showcasing our services to prospective clients.

Attached are a selection of existing stationary and the colour scheme.

Further details on our company can be found at www.velt-advisory-partners.com
Updates

Preference is for bi-fold, however, innovative tri-fold will be considered. Added Monday, August 7, 2017

Target Market(s)

Construction companies, consultants, developers, oil and gas service providers, NGO's, SME's.

Industry/Entity Type

Management

Requirements
Must have
• High degree of professionalism with eye catching, sharp detail. No frils.
• Colour scheme as per the attachments
• Font as per attachments - Century Gothic
• Details of our company and services
Nice to have
• Open to ideas, thinking along the lines of a car brochure type design.
• Bi-fold preferred, by trifold accepted if innovative.
Should not have
• Remove reference to the United Arab Emirates.
• No cartoon/clipart photos.

```html
<!DOCTYPE html>
<html lang="en">
<head>
<meta charset="utf-8">
<title>Velt Advisory – Brochure Spread</title>
<link rel="stylesheet" href="https://fonts.googleapis.com/css2?family=Montserrat:wght@600;700&family=Questrial&display=swap">
<style>
  :root{
    --navy:#2f3f5e;
    --navy-deep:#253350;
    --red:#a8252c;
    --white:#ffffff;
    --mist:#e9edf3;
    --sky:#9fb8d8;
    --steel:#3f5f8f;
    --stage:#d9dce1;
    --text-soft:#c9d1de;
  }
  *{box-sizing:border-box;margin:0;padding:0}
  html,body{width:1200px;height:789px;overflow:hidden}
  body{background:var(--stage);font-family:"Questrial",sans-serif;position:relative}
  .spread{position:absolute;left:105px;top:44px;width:990px;height:700px;display:flex;box-shadow:0 6px 24px rgba(0,0,0,.18)}
  .page{position:relative;width:495px;height:700px;overflow:hidden}

  /* Inside / back page */
  .page--about{background:var(--navy);color:var(--text-soft)}
  .about{position:absolute;left:52px;top:92px;width:395px}
  .about__title{font-family:"Montserrat",sans-serif;font-weight:700;font-size:19px;color:var(--white);letter-spacing:.5px}
  .about__title span{font-family:"Questrial",sans-serif;font-weight:400}
  .about__rule{height:1px;background:var(--text-soft);opacity:.6;margin:8px 0 10px;width:330px}
  .about p{font-size:8.6px;line-height:1.35;margin-bottom:9px}
  .about p.lead{font-size:9.4px}
  .about p.big{font-size:11px;line-height:1.3}
  .sectors{list-style:none;margin:-4px 0 9px}
  .sectors li{font-family:"Montserrat",sans-serif;font-weight:600;font-size:8.6px;color:var(--white);line-height:1.45;padding-left:14px;position:relative}
  .sectors li::before{content:"";position:absolute;left:0;top:3px;width:6px;height:6px;border:1px solid var(--white);border-radius:50%}
  .about .quote{font-family:"Montserrat",sans-serif;font-weight:700;color:var(--white);font-size:9.6px;line-height:1.4}
  .brandmark{position:absolute;display:flex;align-items:center;gap:8px;letter-spacing:1px;white-space:nowrap}
  .brandmark__dot{width:10px;height:10px;border-radius:50%;flex:none}
  .brandmark--about{left:292px;top:572px;font-size:21px;color:var(--white)}
  .brandmark--about .brandmark__dot{background:var(--white)}
  .contacts{position:absolute;left:52px;top:628px;list-style:none;font-size:10px;color:var(--white);line-height:1.7}
  .contacts li{display:flex;align-items:center;gap:8px}
  .contacts svg{width:10px;height:10px}
  .about-strip{position:absolute;right:0;bottom:0;width:210px;height:6px;background:var(--red)}

  /* Front cover */
  .page--cover{background:var(--white)}
  .cover-photo{position:absolute;left:0;top:0;width:495px;height:520px;background:linear-gradient(160deg,var(--mist) 0%,var(--sky) 40%,var(--steel) 75%,var(--navy-deep) 100%)}
  .cover-navy{position:absolute;left:0;top:520px;width:190px;height:180px;background:var(--navy)}
  .cover-red{position:absolute;left:190px;top:520px;width:305px;height:150px;background:var(--red)}
  .cover-logo-panel{position:absolute;right:0;top:410px;width:270px;height:150px;background:var(--white);display:flex;align-items:center;justify-content:center}
  .brandmark--cover{position:static;font-size:22px;color:var(--navy)}
  .brandmark--cover .brandmark__dot{background:var(--red)}
  .cover-title{position:absolute;left:40px;top:572px;color:var(--white);font-family:"Montserrat",sans-serif;font-weight:700;font-size:19px;line-height:1.05;letter-spacing:.3px;white-space:nowrap}
  .cover-title .and{font-family:"Questrial",sans-serif;font-weight:400}
  .cover-title .last{font-size:17px}
  .cover-web{position:absolute;right:22px;top:580px;color:var(--white);font-size:10px;display:flex;align-items:center;gap:6px;white-space:nowrap}
  .cover-web svg{width:10px;height:10px}
</style>
</head>
<body>
<main class="spread">
  <section class="page page--about">
    <div class="about">
      <h2 class="about__title">ABOUT <span>US</span></h2>
      <div class="about__rule"></div>
      <p class="lead">We are an experienced contract and conflict advisory providing global contract performance solutions and conflict management to:</p>
      <ul class="sectors">
        <li>International Development Organisations;</li>
        <li>Construction Industry;</li>
        <li>Oil And Gas Industry; And</li>
        <li>Government Sectors.</li>
      </ul>
      <p>Observing the standard of consultancy services and magnitude of contractual engagements and conflicts, we see the opportunity to make things better: better engagements, better awareness, better performance which all lead to better value in terms of financial benefit and relationship maintenance. We firmly believe in party success in a non litigious environment.</p>
      <p>Our services are uniquely delivered through our integrated management consultancy model, with a single point of contact and responsibility, and focused attention to detail. We provide advisory services and solutions resolving past and current claims, and in doing so, preparing our clients for a conflict free future based on our core principles of integrity, equality and strength, ensuring compliance and experience at an intimate professional level. We aim to have our clients feel our principles in our presence and in our advisories, giving the service which is deserved.</p>
      <p class="big">Our clients range from global Fortune 500 companies, international contractors to government bodies and authorities.</p>
      <p>Velt Advisory is more than just a professional advisory consultancy: we are an integrated professional team with deep domain expertise, industry knowledge and the ability to work across multiple jurisdictions supported by a wide professional network.</p>
      <p>We forge strong client partnerships and in doing so, we develop and maintain these relationships through performance and delivery of professional services which create and maximise value for our clients.</p>
      <p>Through our unique approach to contract and conflict management, we want the best for our clients to ensure that contract integrity, compliance and performance is maintained with the upmost faith, based around our principles.</p>
      <p class="quote">“If value, whether financial or relationship is not achieved, then we are not finished, we have only just begun.”</p>
    </div>
    <div class="brandmark brandmark--about"><span class="brandmark__dot"></span>VELT ADVISORY</div>
    <ul class="contacts">
      <li><svg viewBox="0 0 10 10" fill="none" stroke="currentColor"><rect x="0.5" y="1.5" width="9" height="7"/><path d="M0.5 1.5 5 5.5 9.5 1.5"/></svg>mhale@velt-advisory-partners.com</li>
      <li><svg viewBox="0 0 10 10" fill="none" stroke="currentColor"><circle cx="5" cy="5" r="4.5"/><path d="M0.5 5h9M5 0.5c-2.5 3-2.5 6 0 9M5 0.5c2.5 3 2.5 6 0 9"/></svg>www.velt-advisory-partners.com</li>
    </ul>
    <div class="about-strip"></div>
  </section>

  <section class="page page--cover">
    <div class="cover-photo" role="img" aria-label="Photograph of business people silhouetted shaking hands in a bright glass office, reflected on the floor"></div>
    <div class="cover-navy"></div>
    <div class="cover-red"></div>
    <div class="cover-logo-panel">
      <div class="brandmark brandmark--cover"><span class="brandmark__dot"></span>VELT ADVISORY</div>
    </div>
    <h1 class="cover-title">THE<br>CONTRACT<br><span class="and">AND</span><br><span class="last">CONFLICT ADVISORY</span></h1>
    <div class="cover-web"><svg viewBox="0 0 10 10" fill="none" stroke="currentColor"><circle cx="5" cy="5" r="4.5"/><path d="M0.5 5h9M5 0.5c-2.5 3-2.5 6 0 9M5 0.5c2.5 3 2.5 6 0 9"/></svg>www.velt-advisory-partners.com</div>
  </section>
</main>
</body>
</html>
```